Birchline Septic Solutions

Would like to see some single sided ones but would also like to see some double sided with one sided only being the logo. Owners name is Colin Vandro. Phone number is 555-214-0387
Services are pumping, inspections, installs, and repairs

Contact Information for Business Card

555-241-0387 Colin Vandro Fernbrook, OH

```html
<!DOCTYPE html>
<html lang="en">
<head>
<meta charset="utf-8">
<title>Birchline Septic Solutions — Business Cards</title>
<link rel="stylesheet" href="https://fonts.googleapis.com/css2?family=Montserrat:wght@500;600;800&display=swap">
<style>
  :root {
    --backdrop: #e4e4e4;
    --card-white: #f7f7f7;
    --card-black: #0b0b0b;
    --teal: #2bbfb9;
    --ink: #111111;
    --paper-text: #ffffff;
  }
  * { box-sizing: border-box; margin: 0; padding: 0; }
  html, body {
    width: 1200px;
    height: 930px;
    overflow: hidden;
    background: var(--backdrop);
    font-family: "Montserrat", sans-serif;
  }
  .canvas {
    position: relative;
    width: 1200px;
    height: 930px;
  }
  .card {
    position: absolute;
    width: 640px;
    height: 366px;
    border-radius: 2px;
    box-shadow: 0 6px 18px rgba(0,0,0,0.12);
    overflow: hidden;
  }
  .brand-name {
    position: absolute;
    left: 0; right: 0;
    text-align: center;
    white-space: nowrap;
    font-weight: 800;
    font-size: 34px;
    letter-spacing: 1px;
    text-transform: uppercase;
  }

  /* Back side: logo only with service band */
  .card--back {
    left: 500px;
    top: 90px;
    background: var(--card-black);
  }
  .card--back .brand-name {
    top: 140px;
    color: var(--paper-text);
  }
  .service-band {
    position: absolute;
    left: 0; right: 0; bottom: 0;
    height: 44px;
    background: var(--teal);
    display: flex;
    align-items: center;
    justify-content: space-evenly;
  }
  .service-band li {
    list-style: none;
    font-weight: 600;
    font-size: 17px;
    letter-spacing: 1.5px;
    text-transform: uppercase;
    color: var(--card-black);
  }

  /* Front side: contact details */
  .card--front {
    left: 60px;
    top: 470px;
    background: var(--card-white);
    color: var(--ink);
  }
  .card--front .brand-name {
    top: 70px;
    color: var(--ink);
  }
  .owner-name {
    position: absolute;
    left: 0; right: 0;
    top: 160px;
    text-align: center;
    white-space: nowrap;
    font-weight: 800;
    font-size: 26px;
    letter-spacing: 0.5px;
    text-transform: uppercase;
  }
  .contact-row {
    position: absolute;
    left: 0; right: 0;
    top: 236px;
    display: flex;
    justify-content: center;
    gap: 60px;
  }
  .contact-item {
    display: flex;
    align-items: center;
    gap: 12px;
    white-space: nowrap;
    font-weight: 500;
    font-size: 19px;
    letter-spacing: 0.5px;
  }
  .contact-icon {
    width: 28px;
    height: 28px;
    flex: none;
  }
</style>
</head>
<body>
  <main class="canvas">

    <section class="card card--back" aria-label="Business card back">
      <p class="brand-name">Birchline Septic Solutions</p>
      <ul class="service-band">
        <li>Pumping</li>
        <li>Inspections</li>
        <li>Installs</li>
        <li>Repairs</li>
      </ul>
    </section>

    <section class="card card--front" aria-label="Business card front">
      <p class="brand-name">Birchline Septic Solutions</p>
      <h1 class="owner-name">Colin Vandro</h1>
      <div class="contact-row">
        <p class="contact-item">
          <svg class="contact-icon" viewBox="0 0 28 28" aria-hidden="true">
            <circle cx="14" cy="14" r="14" fill="var(--teal)"/>
            <path d="M10.2 8.2c.5-.4 1.2-.3 1.5.2l1.2 1.9c.3.5.2 1.1-.2 1.4l-.8.6c.6 1.5 1.8 2.8 3.3 3.5l.6-.8c.4-.4 1-.5 1.4-.2l1.9 1.2c.5.3.6 1 .2 1.5l-.9 1.1c-.5.6-1.300.8-2 .5-3.3-1.3-5.8-3.9-7.1-7.2-.3-.7 0-1.5.5-2z" fill="#ffffff"/>
          </svg>
          <span>555-214-0387</span>
        </p>
        <p class="contact-item">
          <svg class="contact-icon" viewBox="0 0 28 28" aria-hidden="true">
            <circle cx="14" cy="14" r="14" fill="var(--teal)"/>
            <path d="M14 6.5a5 5 0 0 0-5 5c0 3.8 5 9.5 5 9.5s5-5.7 5-9.5a5 5 0 0 0-5-5z" fill="#ffffff"/>
            <circle cx="14" cy="11.5" r="1.9" fill="var(--teal)"/>
          </svg>
          <span>Fernbrook, OH</span>
        </p>
      </div>
    </section>

  </main>
</body>
</html>
```